I need a new business card designed, we recently rebranded and I need to get a fresh design to match our new logo, colours and branding.

Details:

Derek Havill | Founder & CEO
Address: 7 Marlowfern Lane, #09-14 Tavenport Crest, Singapore 318547
Tel: +65 93568214
Web: www.frostkarta.com.sg
hello@frostkarta.com.sg

I've attached my old card as well

Industry/Entity Type

Business

Requirements
Must have
• Front and Back
Interesting use of logo
Correct use of colour scheme

```html
<!DOCTYPE html>
<html lang="en">
<head>
<meta charset="utf-8">
<title>frostkarta business card</title>
<link rel="stylesheet" href="https://fonts.googleapis.com/css2?family=Source+Sans+3:wght@400&family=Arimo:wght@400&display=swap">
<style>
  :root {
    --stage: #000000;
    --label: #8a8a8a;
    --sky-1: #93d6f5;
    --sky-2: #55bde9;
    --sky-3: #2ea9e0;
    --taupe: #a09086;
    --bark: #706257;
    --white: #ffffff;
    --ink: #111111;
    --muted: #b9b9b9;
    --back-top: #ffffff;
    --back-bottom: #ebebeb;
  }
  * { margin: 0; padding: 0; box-sizing: border-box; }
  html, body { width: 1200px; height: 1000px; overflow: hidden; background: var(--stage); }
  .stage { position: relative; width: 1200px; height: 1000px; }
  .side-label {
    position: absolute; left: 204px;
    font: 400 24px/1 "Source Sans 3", sans-serif; color: var(--label);
  }
  .side-label--front { top: 86px; }
  .side-label--back { top: 574px; }

  .card { position: absolute; left: 283px; width: 691px; height: 395px; overflow: hidden; }
  .card--front { top: 72px; }
  .card--back {
    top: 557px; height: 396px;
    background: linear-gradient(to bottom, var(--back-top) 15%, var(--back-bottom));
  }
  .stripes { position: absolute; inset: 0; }
  .stripe { height: 65.5px; }
  .stripe--sky-1 { background: var(--sky-1); }
  .stripe--sky-2 { background: var(--sky-2); }
  .stripe--sky-3 { background: var(--sky-3); }
  .stripe--taupe { background: var(--taupe); }
  .stripe--bark { background: var(--bark); }
  .stripe--fade { height: 68px; background: linear-gradient(to bottom, var(--sky-1), var(--sky-3)); }
  .panel { position: absolute; inset: 0; }

  .brand { position: absolute; display: flex; align-items: center; }
  .brand__mark {
    width: 40px; height: 40px;
    background: var(--sky-3);
    margin-right: 14px; flex: none;
  }
  .brand__name {
    font: 400 36px/1 "Source Sans 3", sans-serif; color: var(--ink);
  }
  .card--front .brand { left: 64px; top: 58px; }
  .card--back .brand { left: 250px; top: 178px; }

  .person {
    position: absolute; left: 64px; top: 175px;
    font: 400 31px/1 "Source Sans 3", sans-serif; color: var(--ink);
  }
  .person__role { color: var(--muted); }

  .contact {
    position: absolute; left: 64px; top: 242px;
    font: 400 17px/26.5px "Arimo", sans-serif; color: var(--ink);
    border-collapse: collapse;
  }
  .contact td { padding: 0; }
  .contact__key { width: 85px; }
  .contact__sep { width: 20px; }
  .address {
    position: absolute; left: 66px; top: 345px;
    font: 400 17px/1 "Arimo", sans-serif; color: var(--ink);
  }
</style>
</head>
<body>
<main class="stage">
  <p class="side-label side-label--front">Front</p>
  <section class="card card--front" aria-label="Card front">
    <div class="stripes">
      <div class="stripe stripe--sky-1"></div>
      <div class="stripe stripe--sky-2"></div>
      <div class="stripe stripe--sky-3"></div>
      <div class="stripe stripe--taupe"></div>
      <div class="stripe stripe--bark"></div>
      <div class="stripe stripe--fade"></div>
    </div>
    <svg class="panel" width="691" height="395" viewBox="0 0 691 395" aria-hidden="true">
      <path d="M54 17 H478 Q500 17 510 40 L628 335 Q640 379 600 379 H54 Q24 379 24 349 V47 Q24 17 54 17 Z" fill="var(--white)"/>
    </svg>
    <div class="brand">
      <span class="brand__mark"></span>
      <span class="brand__name">frostkarta</span>
    </div>
    <p class="person">Derek Havill | <span class="person__role">Founder &amp; CEO</span></p>
    <table class="contact">
      <tr><td class="contact__key">Tel</td><td class="contact__sep">:</td><td>+65 93568214</td></tr>
      <tr><td class="contact__key">Web</td><td class="contact__sep">:</td><td>www.frostkarta.com.sg</td></tr>
      <tr><td class="contact__key">e-mail</td><td class="contact__sep">:</td><td>hello@frostkarta.com.sg</td></tr>
    </table>
    <p class="address">7 Marlowfern Lane, #09-14 Tavenport Crest, Singapore 318547</p>
  </section>

  <p class="side-label side-label--back">Back</p>
  <section class="card card--back" aria-label="Card back">
    <div class="brand">
      <span class="brand__mark"></span>
      <span class="brand__name">frostkarta</span>
    </div>
  </section>
</main>
</body>
</html>
```